"How it works" illustration

We are a startup that will sell greeting cards to consumers online. Our value proposition is based on convenient delivery of the cards when customer need them. We need an illustration that shows how things will work for our consumers. This illustration will be the most important element on the landing page of our website. The illustrations should be cartoons or drawings that explain simply what customers need to do on each step required to complete a purchase with us. Attached we have a description of each of the steps. Please prepare two versions, one including only the drawings/cartoons (no text) and another one that includes the attached text. The service is targeted for professional women aged between 25 and 40. The design should communicate simplicity and friendlyness. Some of the colors we have in our logo are white, light blue and light grey (you can see our logo on the second slide of the attached file). As a reference we really like the illustrations used by Tarnwell on their landing page.

```html
<!DOCTYPE html>
<html lang="en">
<head>
<meta charset="utf-8">
<title>How it works</title>
<link rel="stylesheet" href="https://fonts.googleapis.com/css2?family=Source+Sans+3:ital,wght@0,300;0,400;0,700;1,400&display=swap">
<style>
  :root {
    --paper: #ffffff;
    --sky: #3fb1e3;
    --sky-soft: #d6eef9;
    --mist: #eef1f3;
    --ink: #1e1e1e;
    --muted: #8f8f8f;
  }
  * { box-sizing: border-box; margin: 0; padding: 0; }
  html, body {
    width: 1200px;
    height: 900px;
    overflow: hidden;
    background: var(--paper);
  }
  .how-it-works {
    position: relative;
    width: 1200px;
    height: 900px;
    font-family: "Source Sans 3", sans-serif;
    color: var(--ink);
  }
  .step-art {
    position: absolute;
    top: 96px;
    width: 280px;
    height: 250px;
    border-radius: 14px;
    background: linear-gradient(160deg, var(--sky-soft) 0%, var(--mist) 75%);
  }
  .step-art--signup  { left: 62px; }
  .step-art--confirm { left: 460px; }
  .step-art--deliver { left: 846px; }
  .step-number {
    position: absolute;
    top: 376px;
    width: 68px;
    height: 68px;
    border-radius: 50%;
    background: var(--sky);
    color: var(--paper);
    font-size: 44px;
    font-weight: 300;
    line-height: 68px;
    text-align: center;
  }
  .step-number--1 { left: 168px; }
  .step-number--2 { left: 566px; }
  .step-number--3 { left: 952px; }
  .step-copy {
    position: absolute;
    top: 450px;
    width: 340px;
  }
  .step-copy--signup  { left: 52px; }
  .step-copy--confirm { left: 444px; }
  .step-copy--deliver { left: 839px; }
  .step-title {
    color: var(--sky);
    font-size: 20px;
    font-weight: 700;
    line-height: 22px;
    margin-bottom: 1px;
  }
  .step-body,
  .step-aside {
    font-size: 15.5px;
    line-height: 19.5px;
  }
  .step-aside {
    margin-top: 19px;
    color: var(--muted);
    font-style: italic;
  }
  .line {
    display: block;
    white-space: nowrap;
  }
</style>
</head>
<body>
<main class="how-it-works">
  <div class="step-art step-art--signup" role="img" aria-label="Drawing of a woman at a desktop computer filling in a sign-up form"></div>
  <div class="step-art step-art--confirm" role="img" aria-label="Drawing of a computer screen showing a blue elephant mascot holding an envelope, with a speech bubble birthday reminder"></div>
  <div class="step-art step-art--deliver" role="img" aria-label="Drawing of a woman waving at a flying blue elephant mascot carrying envelopes over clouds and a sketched globe"></div>

  <div class="step-number step-number--1">1</div>
  <div class="step-number step-number--2">2</div>
  <div class="step-number step-number--3">3</div>

  <section class="step-copy step-copy--signup">
    <h2 class="step-title">SIGN UP</h2>
    <p class="step-body">
      <span class="line">Sign up and select all the greeting cards you</span>
      <span class="line">wish to send during next year (tell us who</span>
      <span class="line">you are sending them to, why and by when</span>
      <span class="line">do you need them)</span>
    </p>
    <p class="step-aside">
      <span class="line">After that you are done and can relax (maybe</span>
      <span class="line">go to the beach on vacation). You don’t have to</span>
      <span class="line">worry anymore about forgetting sending a</span>
      <span class="line">greeting card to that person that really, REALLY</span>
      <span class="line">was expecting one</span>
    </p>
  </section>

  <section class="step-copy step-copy--confirm">
    <h2 class="step-title">CONFIRM</h2>
    <p class="step-body">
      <span class="line">Two weeks before every event we’ll send you</span>
      <span class="line">a reminder asking you to confirm your card</span>
      <span class="line">design and delivery method (directly to</span>
      <span class="line">recipient or to you first)</span>
    </p>
    <p class="step-aside">
      <span class="line">Don’t worry, we won’t harass you with emails.</span>
      <span class="line">We’ll only send them when its convenient to</span>
      <span class="line">you and we’ll make the confirmation process</span>
      <span class="line">simple… We promise</span>
    </p>
  </section>

  <section class="step-copy step-copy--deliver">
    <h2 class="step-title">DELIVER</h2>
    <p class="step-body">
      <span class="line">Depending on the delivery method you</span>
      <span class="line">chose we can either:</span>
      <span class="line">1)Send the card directly to the recipient with</span>
      <span class="line">your message printed on the card, or</span>
      <span class="line">2)Send the card to you with a “ready to</span>
      <span class="line">re-send envelope” (yes, postage and every-</span>
      <span class="line">thing!) so you just have to open up the card,</span>
      <span class="line">sign it and put it back in the mail.</span>
    </p>
    <p class="step-aside">
      <span class="line">Simple right? Now give it a try and enjoy the</span>
      <span class="line">feeling of being an amazing, thoughtful, kind,</span>
      <span class="line">smart individual and all other compliments</span>
      <span class="line">that will be given to you just for sending this</span>
      <span class="line">amazing greeting cards</span>
    </p>
  </section>
</main>
</body>
</html>
```